Business card for medical clinic

I need an upmarket, modern medical/health business card for my clinic

Contact Information for Business Card

name, address, email, qr code

```html
<!DOCTYPE html>
<html lang="en">
<head>
<meta charset="utf-8">
<title>Meridan Care Partners – Business Card</title>
<link rel="stylesheet" href="https://fonts.googleapis.com/css2?family=Poppins:wght@300;400;500;700&display=swap">
<style>
  :root {
    --backdrop: #222222;
    --card: #ffffff;
    --navy: #1d4f7c;
    --sky: #1f9ad6;
    --ink: #111111;
    --edge: #2a9be0;
  }
  * { margin: 0; padding: 0; box-sizing: border-box; }
  html, body { width: 1200px; height: 711px; overflow: hidden; background: var(--backdrop); }
  body { font-family: "Poppins", sans-serif; position: relative; }

  .card {
    position: absolute;
    top: 212px;
    width: 500px;
    height: 286px;
    background: var(--card);
    border-bottom: 4px solid var(--edge);
    border-left: 3px solid var(--edge);
  }
  .card--front { left: 66px; }
  .card--back { left: 634px; }

  .brand {
    position: absolute;
    display: flex;
    align-items: center;
    gap: 12px;
    color: var(--navy);
    font-weight: 500;
    letter-spacing: 0.04em;
    text-transform: uppercase;
    white-space: nowrap;
  }
  .card--front .brand { left: 50%; top: 50%; transform: translate(-50%, -50%); font-size: 22px; }
  .card--back .brand {
    left: 26px;
    top: 160px;
    width: 196px;
    font-size: 13px;
    line-height: 1.3;
    gap: 10px;
    white-space: normal;
  }
  .brand__circle { flex: none; border: 3px solid var(--sky); border-radius: 50%; }
  .card--front .brand__circle { width: 54px; height: 54px; }
  .card--back .brand__circle { width: 40px; height: 40px; border-width: 2px; }

  .divider {
    position: absolute;
    left: 242px;
    top: 70px;
    width: 1px;
    height: 140px;
    background: var(--sky);
  }

  .person { position: absolute; left: 262px; top: 58px; }
  .person__name { font-size: 30px; line-height: 1; color: var(--sky); white-space: nowrap; }
  .person__first { font-weight: 700; }
  .person__last { font-weight: 300; }
  .person__role { font-size: 12px; font-weight: 500; color: var(--ink); margin-top: 4px; }

  .contacts { list-style: none; margin-top: 14px; }
  .contacts li {
    display: flex;
    align-items: center;
    gap: 8px;
    font-size: 12.5px;
    color: var(--ink);
    line-height: 1.6;
  }
  .contacts svg { width: 13px; height: 13px; flex: none; fill: var(--sky); }

  .address {
    position: absolute;
    right: 26px;
    bottom: 22px;
    font-size: 13px;
    color: var(--sky);
    white-space: nowrap;
  }
</style>
</head>
<body>
  <section class="card card--front" aria-label="Card front">
    <div class="brand"><span class="brand__circle"></span>Meridan Care Partners</div>
  </section>

  <section class="card card--back" aria-label="Card back">
    <div class="brand"><span class="brand__circle"></span><span>Meridan Care Partners</span></div>
    <div class="divider"></div>
    <div class="person">
      <h1 class="person__name"><span class="person__first">Marta</span> <span class="person__last">Novell</span></h1>
      <p class="person__role">Founder &amp; CEO</p>
      <ul class="contacts">
        <li>
          <svg viewBox="0 0 24 24" aria-hidden="true"><path d="M6.6 10.8a15.2 15.2 0 0 0 6.6 6.6l2.2-2.2a1 1 0 0 1 1-.25 11.4 11.4 0 0 0 3.6.57 1 1 0 0 1 1 1V20a1 1 0 0 1-1 1A17 17 0 0 1 3 4a1 1 0 0 1 1-1h3.5a1 1 0 0 1 1 1c0 1.250.2 2.45.57 3.57a1 1 0 0 1-.25 1z"/></svg>
          (555) 204-1187
        </li>
        <li>
          <svg viewBox="0 0 24 24" aria-hidden="true"><path d="M20 4H4a2 2 0 0 0-2 2v12a2 2 0 0 0 2 2h16a2 2 0 0 0 2-2V6a2 2 0 0 0-2-2zm0 4-8 5-8-5V6l8 5 8-5z"/></svg>
          info@meridancare.com
        </li>
        <li>
          <svg viewBox="0 0 24 24" aria-hidden="true"><path d="M12 2a10 10 0 1 0 0 20 10 10 0 0 0 0-20zm6.9 6h-2.9a15.7 15.7 0 0 0-1.4-3.6A8 8 0 0 1 18.9 8zM12 4a14 14 0 0 1 1.9 4h-3.8A14 14 0 0 1 12 4zM4.3 14a8 8 0 0 1 0-4h3.4a16.5 16.5 0 0 0 0 4zm.8 2h2.9a15.7 15.7 0 0 0 1.4 3.6A8 8 0 0 1 5.1 16zM8 8H5.1a8 8 0 0 1 4.3-3.6A15.7 15.7 0 0 0 8 8zm4 12a14 14 0 0 1-1.9-4h3.8A14 14 0 0 1 12 20zm2.3-6H9.7a14.7 14.7 0 0 1 0-4h4.6a14.7 14.7 0 0 1 0 4zm.3 5.6a15.7 15.7 0 0 0 1.4-3.6h2.9a8 8 0 0 1-4.3 3.6zm1.7-5.6a16.5 16.5 0 0 0 0-4h3.4a8 8 0 0 1 0 4z"/></svg>
          www.meridancare.com
        </li>
      </ul>
    </div>
    <p class="address">4180 Linden Ave. Suite 310 Oak Harbor, TX 75010</p>
  </section>
</body>
</html>
```